Brell Stone Company Business Cards

Front and Back Business Card - logo and text setup - cool design. I need workable photoshop or illustrator files so I can setup each employee card with design that is created
Updates

Hi everyone, thank you for the great entries. Please no more white and blue cards - there are so many already - black and silver only now please. thanks!

Target Market(s)

Construction Industry - Facility Managers

Industry/Entity Type

Construction

Contact Information for Business Card

I really like contemporary simplistic looks - clean neat....not opposed to seeing some black backrounds

Requirements
Must have
• Logo/website address with design on front only - www.brellstone-example.com (logo attached)
• Back:
• Name/Title/Company Address/Phone/email address
Nice to have
• Cool design
Should not have
• Nothing gimmicky like Fire or Water - since we are a Fire Protection company - it has all been done

```html
<!DOCTYPE html>
<html lang="en">
<head>
<meta charset="utf-8">
<title>Brell Stone Company Business Cards</title>
<link rel="stylesheet" href="https://fonts.googleapis.com/css2?family=Open+Sans:ital,wght@0,400;0,700;0,800;1,700&display=swap">
<style>
  :root {
    --page: #1c1c1e;
    --card-dark: #141414;
    --card-sheen: #2e2e2f;
    --brand-blue: #0a2396;
    --brand-red: #f8231e;
    --text-light: #f2f2f2;
    --text-grey: #c9c9c9;
  }
  * { box-sizing: border-box; margin: 0; padding: 0; }
  html, body { width: 1200px; height: 960px; overflow: hidden; }
  body {
    background: var(--page);
    font-family: "Open Sans", Arial, sans-serif;
    display: flex;
    flex-direction: column;
    align-items: center;
    justify-content: center;
    gap: 40px;
  }
  .card {
    position: relative;
    width: 700px;
    height: 400px;
    border-radius: 6px;
    overflow: hidden;
    background:
      linear-gradient(100deg, transparent 30%, rgba(255,255,255,0.07) 48%, transparent 62%),
      repeating-linear-gradient(90deg, rgba(255,255,255,0.018) 0 1px, transparent 1px 3px),
      linear-gradient(180deg, var(--card-sheen), var(--card-dark) 60%);
    box-shadow: 0 14px 30px rgba(0,0,0,0.45);
  }
  .wordmark {
    font-weight: 800;
    color: var(--brand-red);
    letter-spacing: -0.5px;
    line-height: 1;
  }
  /* Front */
  .card-front .wordmark {
    position: absolute;
    top: 130px; left: 0; right: 0;
    text-align: center;
    font-size: 68px;
  }
  .card-front .website {
    position: absolute;
    top: 240px; left: 0; right: 0;
    text-align: center;
    font-size: 17px;
    letter-spacing: 4px;
    color: var(--text-grey);
  }
  /* Back */
  .card-back .wordmark {
    position: absolute;
    top: 52px; left: 40px;
    font-size: 50px;
  }
  .info-band {
    position: absolute;
    left: 0; right: 0; bottom: 0;
    height: 215px;
    background: var(--brand-blue);
    border-top: 3px solid var(--brand-red);
    z-index: 1;
  }
  .contact-list {
    position: absolute;
    top: 38px; left: 30px;
    list-style: none;
    color: var(--text-light);
    font-size: 16px;
  }
  .contact-list li {
    display: flex; align-items: center; gap: 12px;
    height: 30px;
    white-space: nowrap;
  }
  .contact-list svg { width: 16px; height: 16px; flex: none; }
  .divider {
    position: absolute;
    top: 60px; left: 330px;
    width: 1px; height: 90px;
    background: rgba(255,255,255,0.45);
  }
  .address {
    position: absolute;
    top: 78px; left: 356px;
    color: var(--text-light);
    font-size: 18px;
    font-style: normal;
    line-height: 1.45;
  }
  .name-tab {
    position: absolute;
    right: 0; top: 150px;
    width: 230px; height: 82px;
    background: var(--brand-red);
    border-radius: 10px 0 0 10px;
    color: #fff;
    text-align: right;
    padding: 12px 24px 0 0;
    font-style: italic;
    font-weight: 700;
    line-height: 1.3;
    z-index: 2;
  }
  .name-tab .person { font-size: 21px; display: block; }
  .name-tab .role { font-size: 21px; display: block; }
</style>
</head>
<body>
  <section class="card card-front" aria-label="Card front">
    <p class="wordmark">Brell Stone</p>
    <p class="website">www.brellstone-example.com</p>
  </section>

  <section class="card card-back" aria-label="Card back">
    <p class="wordmark">Brell Stone</p>
    <div class="info-band">
      <ul class="contact-list">
        <li>
          <svg viewBox="0 0 16 16" aria-hidden="true"><path fill="#fff" d="M3.6 1.2l2.3 2.6-1.3 1.7c.9 2 2.9 4 5 5l1.6-1.4 2.6 2.3-1.4 2.3C7.3 15.3.8 8.7 1.3 2.6z"/></svg>
          (555) 014-2290
        </li>
        <li>
          <svg viewBox="0 0 16 16" aria-hidden="true"><rect x="1" y="3" width="14" height="10" fill="#fff"/><path d="M1.5 3.5L8 9l6.5-5.5" fill="none" stroke="#0a2396" stroke-width="1.3"/></svg>
          info@brellstone-example.com
        </li>
        <li>
          <svg viewBox="0 0 16 16" aria-hidden="true"><g fill="none" stroke="#fff" stroke-width="1.3"><circle cx="8" cy="8" r="6.5"/><ellipse cx="8" cy="8" rx="2.8" ry="6.5"/><path d="M1.5 8h13M2.6 4.5h10.8M2.6 11.5h10.8"/></g></svg>
          www.brellstone-example.com
        </li>
      </ul>
      <span class="divider"></span>
      <address class="address">48 Quarry Lane<br>Millbrook, NY 10000</address>
    </div>
    <div class="name-tab">
      <span class="person">Dana Whitfield</span>
      <span class="role">President</span>
    </div>
  </section>
</body>
</html>
```